Structural Engineering Business Card

Brookvane Drafting does residential house plans for clients in Central Florida. Would like simple but elegant business card that is appropriate for a house plan engineering company. Prefer black business card with black/white them but open to other shades of blue. I uploaded a sample card that I came across that looked good but please come up with your own creative designs.

Contact Information for Business Card

Name, Title, Phone, Email, Address, website

```html
<!DOCTYPE html>
<html lang="en">
<head>
<meta charset="utf-8">
<title>Brookvane Drafting – Business Card</title>
<link href="https://fonts.googleapis.com/css2?family=Poppins:wght@400;600;800&display=swap" rel="stylesheet">
<style>
  :root {
    --backdrop: #2b2b2d;
    --card-black: #0e0e0f;
    --pattern-dark: #1a1a1c;
    --pattern-light: #2c2c2f;
    --card-white: #ffffff;
    --ink: #111111;
    --ink-soft: #3a3a3a;
    --rule: #c8c8c8;
  }
  * { margin: 0; padding: 0; box-sizing: border-box; }
  html, body { width: 1200px; height: 689px; overflow: hidden; }
  body {
    background: var(--backdrop);
    font-family: "Poppins", sans-serif;
    position: relative;
  }
  .card {
    position: absolute;
    top: 196px;
    width: 520px;
    height: 297px;
    border-radius: 18px;
    overflow: hidden;
    box-shadow: 0 18px 40px rgba(0,0,0,0.45);
  }
  /* back face */
  .card--back { left: 50px; background: var(--card-black); }
  .brand-pattern {
    position: absolute; inset: 0;
    background: linear-gradient(135deg, var(--pattern-dark) 0%, var(--pattern-light) 55%, var(--pattern-dark) 100%);
  }
  .card--back .brand-name {
    position: absolute;
    left: 282px; top: 196px;
    color: var(--card-white);
    font-weight: 800;
    font-size: 19px;
    letter-spacing: 0.3px;
  }
  /* front face */
  .card--front { left: 630px; background: var(--card-white); }
  .card--front .brand-name {
    position: absolute;
    left: 28px; top: 128px;
    width: 225px;
    color: var(--ink);
    font-weight: 800;
    font-size: 25px;
    line-height: 1.1;
    text-transform: uppercase;
  }
  .divider {
    position: absolute;
    left: 270px; top: 60px;
    width: 1px; height: 180px;
    background: linear-gradient(to bottom, transparent, var(--rule) 20%, var(--rule) 80%, transparent);
  }
  .contact {
    position: absolute;
    left: 292px; top: 62px;
    color: var(--ink);
  }
  .contact__name { font-weight: 800; font-size: 17px; line-height: 1.1; }
  .contact__title { font-weight: 400; font-size: 12px; color: var(--ink-soft); margin-bottom: 16px; }
  .contact__list { list-style: none; font-size: 12px; line-height: 1.45; color: var(--ink-soft); }
  .contact__list li { display: flex; align-items: flex-start; gap: 7px; }
  .contact__list li.address { margin-top: 10px; }
  .contact__list svg { width: 11px; height: 11px; margin-top: 3px; flex: none; fill: var(--ink); }
</style>
</head>
<body>
  <section class="card card--back">
    <div class="brand-pattern" role="img" aria-label="Faint repeated brand name pattern across the card back"></div>
    <span class="brand-name">Brookvane Drafting</span>
  </section>

  <section class="card card--front">
    <span class="brand-name">Brookvane Drafting</span>
    <div class="divider"></div>
    <div class="contact">
      <p class="contact__name">MARCUS HALE</p>
      <p class="contact__title">Managing Director</p>
      <ul class="contact__list">
        <li><svg viewBox="0 0 24 24"><path d="M6.6 10.8a15 15 0 0 0 6.6 6.6l2.2-2.2c.3-.3.7-.4 1-.2 1.1.4 2.3.6 3.6.6.6 0 1 .4 1 1V20c0 .6-.4 1-1 1A17 17 0 0 1 3 4c0-.6.4-1 1-1h3.5c.6 0 1 .4 1 1 0 1.3.2 2.5.6 3.6.1.3 0 .7-.2 1z"/></svg>044-123 456 789</li>
        <li><svg viewBox="0 0 24 24"><path d="M2 5h20v14H2zm2 2v.5l8 5 8-5V7z"/></svg>info@email.com</li>
        <li><svg viewBox="0 0 24 24"><path d="M12 2a10 10 0 1 0 0 20 10 10 0 0 0 0-20zm1 17.9V17h-2v2.9A8 8 0 0 1 4.1 13H7v-2H4.1A8 8 0 0 1 11 4.1V7h2V4.1a8 8 0 0 1 6.9 6.9H17v2h2.9a8 8 0 0 1-6.9 6.9z"/></svg>www.website.com</li>
        <li class="address"><svg viewBox="0 0 24 24"><path d="M12 2a7 7 0 0 0-7 7c0 5 7 13 7 13s7-8 7-13a7 7 0 0 0-7-7zm0 9.5A2.5 2.5 0 1 1 12 6.5a2.5 2.5 0 0 1 0 5z"/></svg><span>123, 7th street<br>Country name, 123456</span></li>
      </ul>
    </div>
  </section>
</body>
</html>
```